Mobile Fitness snd Therapy Business Card Design

I need a business card designed for my mobile fitness and therapy business.

Please view the images that I have uploaded. I like the simplicity of the design that I have attached. I adapted it with my information

Target Market(s)

Those seeking personal training, injury rehabilitation or massage therapy.

Industry/Entity Type

Business

Contact Information for Business Card

Derek Fulham - MSc, CAT(C), RMT, CSCS, Pn2
e-mail: derek@vantrelo.com
website: www.vantrelo.com
instagram: @derek_fulham

Font styles to use
Sans Serif

Colors
3176b5
0355a3

Requirements
Must have
• "Contact us to receive a FREE assessment"
• Services offered:
• Personal Training
• Golf Fitness
• Injury Rehab
• Massage Therapy
• Yoga
Nice to have
• Consistent colours with brand
• - Dark Blue: #232837
• - Blue: #5096f0
• Consistent look/feel with the website: www.vantrelo.com

```html
<!DOCTYPE html>
<html lang="en">
<head>
<meta charset="utf-8">
<title>Vantrelo Business Card</title>
<link rel="stylesheet" href="https://fonts.googleapis.com/css2?family=Roboto:wght@400;500;700&display=swap">
<style>
  :root {
    --backdrop: #e9ebef;
    --card-light: #f7f7f8;
    --card-dark: #232837;
    --brand-navy: #232837;
    --brand-blue: #5096f0;
    --cta-blue: #1f5fd6;
    --name-blue: #8cbaf2;
    --accent-bar: #3a73e0;
    --text-light: #ffffff;
  }
  * { margin: 0; padding: 0; box-sizing: border-box; }
  html, body {
    width: 1200px; height: 900px; overflow: hidden;
    background: var(--backdrop);
    font-family: "Roboto", Arial, sans-serif;
  }
  .business-card {
    position: absolute; left: 120px; top: 153px;
    width: 960px; height: 594px;
    background: var(--card-light);
    box-shadow: 0 18px 40px rgba(20, 24, 40, 0.18);
    overflow: hidden;
  }
  .brand-panel {
    position: absolute; left: 0; top: 0; width: 100%; height: 308px;
    text-align: center;
  }
  .brand-name {
    position: absolute; left: 0; right: 0; top: 68px;
    font-size: 92px; font-weight: 500; letter-spacing: 8px; line-height: 1;
    color: var(--brand-navy);
  }
  .brand-tagline {
    position: absolute; left: 0; right: 0; top: 172px;
    font-size: 27px; font-weight: 700; letter-spacing: 5px;
    color: var(--brand-navy);
  }
  .cta {
    position: absolute; left: 0; right: 0; top: 223px;
    font-size: 25px; font-weight: 700; letter-spacing: 0.5px;
    color: var(--cta-blue);
  }
  .info-panel {
    position: absolute; left: 0; top: 308px; width: 100%; height: 286px;
    background: var(--card-dark);
  }
  .accent-bar { position: absolute; width: 14px; background: var(--accent-bar); }
  .accent-bar--left { left: 0; top: 51px; bottom: 0; }
  .accent-bar--right { right: 0; top: 68px; bottom: 0; background: var(--brand-blue); }
  .contact-block { position: absolute; left: 54px; top: 44px; }
  .person-name {
    font-size: 31px; font-weight: 700; color: var(--name-blue); line-height: 1.1;
  }
  .credentials {
    margin-top: 8px; font-size: 25px; color: var(--brand-blue);
  }
  .contact-list { list-style: none; margin-top: 26px; }
  .contact-list li {
    display: flex; align-items: center; gap: 8px;
    font-size: 25px; color: var(--text-light); height: 36px;
  }
  .contact-icon { width: 22px; height: 22px; flex: none; }
  .services {
    position: absolute; right: 35px; top: 40px;
    list-style: none; text-align: right;
  }
  .services li {
    font-size: 25px; color: var(--text-light); line-height: 40px;
  }
</style>
</head>
<body>
  <div class="business-card">
    <header class="brand-panel">
      <div class="brand-name">VANTRELO</div>
      <div class="brand-tagline">NUTRITION - FITNESS - HEALTH</div>
      <div class="cta">CONTACT US TO RECEIVE A FREE ASSESSMENT</div>
    </header>
    <section class="info-panel">
      <span class="accent-bar accent-bar--left"></span>
      <span class="accent-bar accent-bar--right"></span>
      <div class="contact-block">
        <div class="person-name">DEREK FULHAM</div>
        <div class="credentials">MSc, CAT(C), RMT, CSCS, Pn2</div>
        <ul class="contact-list">
          <li>
            <svg class="contact-icon" viewBox="0 0 22 22" aria-hidden="true">
              <rect x="2" y="5" width="18" height="13" rx="1" fill="#5096f0"/>
              <path d="M2 6 L11 13 L20 6" fill="none" stroke="#232837" stroke-width="1.8"/>
            </svg>
            derek@vantrelo.com
          </li>
          <li>
            <svg class="contact-icon" viewBox="0 0 22 22" aria-hidden="true">
              <circle cx="11" cy="11" r="9" fill="#5096f0"/>
              <path d="M2 11 H20 M11 2 C6 7 6 15 11 20 M11 2 C16 7 16 15 11 20" fill="none" stroke="#232837" stroke-width="1.4"/>
            </svg>
            www.vantrelo.com
          </li>
          <li>
            <svg class="contact-icon" viewBox="0 0 22 22" aria-hidden="true">
              <circle cx="11" cy="11" r="9" fill="#5096f0"/>
            </svg>
            @derek_fulham
          </li>
        </ul>
      </div>
      <ul class="services">
        <li>Personal Training</li>
        <li>Golf Fitness</li>
        <li>Injury Rehab</li>
        <li>Massage Therapy</li>
        <li>Yoga</li>
      </ul>
    </section>
  </div>
</body>
</html>
```